Vision, Mission and Culture Posters

We have written text paragraphs for our company vision and mission and need them made into a2 or a3 sized posters using our logo for inspiration for colour. Our company culture has 10 paragraphs and we'd like this to be a single poster of a2 or a1. Each poster should have the logo on and share common design. It's not a complex job really.

Industry/Entity Type

It Company

Requirements
Nice to have
• These will be going up on our office wall so need to be clear to read from a distance and look professional but also not stodgy.

```html
<!DOCTYPE html>
<html lang="en">
<head>
<meta charset="utf-8">
<title>Kerbside Bay Rentals – Mission</title>
<link href="https://fonts.googleapis.com/css2?family=Oswald:wght@600;700&family=Roboto+Condensed:ital,wght@0,400;0,700;1,700&family=Rubik:wght@800&display=swap" rel="stylesheet">
<style>
  :root {
    --yellow: #fff200;
    --yellow-soft: #f7ee6a;
    --red: #d2232a;
    --black: #111;
    --white: #fff;
    --ink-dark: #1a1a10;
  }
  * { margin: 0; padding: 0; box-sizing: border-box; }
  html, body { width: 849px; height: 1200px; overflow: hidden; background: var(--white); }
  .poster { position: relative; width: 849px; height: 1200px; background: var(--white); font-family: "Roboto Condensed", sans-serif; }
  .poster__art { position: absolute; inset: 0; }
  .header-tab {
    position: absolute; left: 163px; top: 68px; width: 514px; height: 82px;
    background: var(--ink-dark); border: 2px solid var(--black); border-radius: 14px;
    box-shadow: 0 0 0 3px var(--white), 0 0 0 5px var(--black);
    display: flex; align-items: center; justify-content: center;
  }
  .header-tab__name {
    font-family: "Oswald", sans-serif; font-weight: 700; font-size: 41px;
    color: var(--yellow); letter-spacing: 0.5px; text-transform: uppercase;
  }
  .title {
    position: absolute; left: 0; right: 0; top: 160px; text-align: center;
    font-family: "Oswald", sans-serif; font-weight: 600; font-size: 118px; line-height: 1;
    color: var(--red); transform: scaleX(0.86);
  }
  .mission { position: absolute; left: 60px; right: 60px; top: 430px; text-align: center; color: var(--white); }
  .mission__intro { font-size: 21px; line-height: 30px; }
  .mission__highlight {
    font-family: "Rubik", sans-serif; font-weight: 800; font-size: 33px; line-height: 38px;
    color: var(--yellow); letter-spacing: -0.3px;
  }
  .mission__belief {
    margin-top: 26px; font-weight: 700; font-size: 24.5px; line-height: 35px; color: var(--black);
  }
  .mission__belief em { font-family: "Rubik", sans-serif; font-weight: 800; font-style: italic; color: var(--white); }
  .mission__method { margin-top: 22px; font-size: 22px; line-height: 30px; }
  .mission__close { font-weight: 700; font-size: 26px; line-height: 30px; }
  .brand-box {
    position: absolute; left: 166px; top: 1006px; width: 511px; height: 146px;
    background: linear-gradient(180deg, #eef04a, #e2e43a); border: 2px solid var(--black); border-radius: 12px;
    box-shadow: 0 0 0 3px var(--white), 0 0 0 5px var(--black);
    display: flex; align-items: center; gap: 22px; padding-left: 34px;
  }
  .brand-box__mark { width: 60px; height: 60px; background: var(--red); border: 2px solid var(--black); }
  .brand-box__name { font-weight: 700; font-size: 40px; line-height: 1.05; color: var(--black); }
</style>
</head>
<body>
<main class="poster">
  <svg class="poster__art" width="849" height="1200" viewBox="0 0 849 1200" aria-hidden="true">
    <defs>
      <radialGradient id="panelGlow" cx="50%" cy="55%" r="65%">
        <stop offset="0" stop-color="#f6ef8c"/>
        <stop offset="0.6" stop-color="#f7ee55"/>
        <stop offset="1" stop-color="#fff200"/>
      </radialGradient>
    </defs>
    <!-- framed panel -->
    <rect class="panel" x="34" y="110" width="771" height="964" fill="url(#panelGlow)" stroke="#111" stroke-width="2"/>
    <rect x="40" y="116" width="759" height="952" fill="none" stroke="#111" stroke-width="1"/>
    <g fill="#fff200" stroke="#111" stroke-width="1.5">
      <rect x="44" y="120" width="10" height="10"/>
      <rect x="785" y="120" width="10" height="10"/>
      <rect x="44" y="1054" width="10" height="10"/>
      <rect x="785" y="1054" width="10" height="10"/>
    </g>
    <!-- layered ellipses -->
    <ellipse cx="436" cy="637" rx="348" ry="332" fill="#1a1a10"/>
    <ellipse cx="420" cy="640" rx="392" ry="298" transform="rotate(-4 420 640)" fill="#fff"/>
    <ellipse cx="420" cy="640" rx="383" ry="289" transform="rotate(-4 420 640)" fill="var(--red)"/>
  </svg>

  <header class="header-tab"><span class="header-tab__name">Kerbside Bay Rentals</span></header>
  <h1 class="title">MISSION</h1>

  <section class="mission">
    <p class="mission__intro">Our mission is to</p>
    <p class="mission__highlight">achieve great customer satisfaction</p>
    <p class="mission__intro">in everything we do and offer for meeting our<br>customers’ parking needs.</p>
    <p class="mission__belief">We believe our path to achieving this comes through<br>giving a <em>simple</em> yet thorough and <em>friendly service</em><br>to our customers without unnecessary complication.</p>
    <p class="mission__method">We will achieve this through using the technology available to us,<br>continual staff training and development, regular refinement of<br>our practices and processes along with commitment to<br>our roles and the foundations</p>
    <p class="mission__close">for building our success.</p>
  </section>

  <footer class="brand-box">
    <span class="brand-box__mark"></span>
    <span class="brand-box__name">Kerbside Bay<br>Rentals</span>
  </footer>
</main>
</body>
</html>
```